Business Card Design needed - Something Awesome!

Need a business card designed. Company is "Marlowe Advisory" we do consulting and also have sales automation technology.
I'm going to use thick stock or metal, something really nice... I was thinking about a QR Code on the back that would just upload my contact info to the persons contact, etc -

This is a Strategy Company with a tech feel. I'm open to ideas but really want this to be nice!

I need a template that should include:

Name | Position or Title
D: 415.902.3376
www.marloweadvisory.example

I'm going to attach my contact so you can use that one, I need to get this printed.

Target Market(s)

Small to mid size customers, Entrepreneurs etc.

Industry/Entity Type

Consulting, Tech, Private Equity.

Contact Information for Business Card

Name, Phone, Maybe email, URL

Font styles to use
Sans Serif

Colors

Designer to choose only greyscale colors for use in the design.

Requirements
Must have
• Fresh, Clean, stand out from the crowd - will be on thick stock or metal.
Nice to have
• Clean, simple yet impactful.
Should not have
• Not cartoonish

```html
<!DOCTYPE html>
<html lang="en">
<head>
<meta charset="utf-8">
<title>Marlowe Advisory — Business Card</title>
<link rel="stylesheet" href="https://fonts.googleapis.com/css2?family=Poppins:wght@400;500;600&display=swap">
<style>
  :root {
    --backdrop: #d9d9d9;
    --backdrop-light: #ececec;
    --paper: #fbfbfb;
    --ink: #111111;
    --ink-soft: #3a3a3a;
    --card-black: #050505;
    --card-white-text: #ffffff;
    --shadow: rgba(0, 0, 0, 0.18);
  }
  * { box-sizing: border-box; margin: 0; padding: 0; }
  html, body {
    width: 1200px;
    height: 930px;
    overflow: hidden;
  }
  body {
    background: radial-gradient(ellipse at 50% 45%, var(--backdrop-light) 0%, var(--backdrop) 100%);
    font-family: "Poppins", sans-serif;
    display: flex;
    align-items: center;
    justify-content: center;
    gap: 44px;
  }
  .card {
    width: 525px;
    height: 300px;
    border-radius: 2px;
    box-shadow: 0 14px 30px var(--shadow);
    position: relative;
  }
  .card--front {
    background: var(--paper);
    color: var(--ink);
    padding: 56px 0 0 70px;
  }
  .wordmark {
    font-weight: 500;
    font-size: 40px;
    letter-spacing: 1px;
    line-height: 1;
    text-transform: uppercase;
    display: flex;
    align-items: center;
    gap: 14px;
  }
  .wordmark__square {
    width: 18px;
    height: 18px;
    background: currentColor;
    flex: none;
  }
  .contact {
    margin-top: 30px;
    margin-left: 32px;
    font-size: 15px;
    line-height: 1.4;
    color: var(--ink);
  }
  .contact__name {
    font-weight: 600;
    font-size: 15px;
    letter-spacing: 0.5px;
    text-transform: uppercase;
  }
  .contact__title {
    font-size: 11px;
    letter-spacing: 1px;
    text-transform: uppercase;
    color: var(--ink-soft);
    margin-bottom: 6px;
  }
  .contact__line { font-size: 15px; }
  .card--back {
    background: var(--card-black);
    color: var(--card-white-text);
    display: flex;
    align-items: center;
    justify-content: center;
  }
  .card--back .wordmark {
    font-size: 30px;
    letter-spacing: 2px;
  }
  .card--back .wordmark__square {
    width: 22px;
    height: 22px;
  }
</style>
</head>
<body>
  <article class="card card--front">
    <div class="wordmark">
      <span class="wordmark__name">Marlowe Advisory</span>
    </div>
    <div class="contact">
      <p class="contact__name">Daniel Reyes</p>
      <p class="contact__title">Managing Director</p>
      <p class="contact__line">415.902.3376</p>
      <p class="contact__line">info@marloweadvisory.example</p>
      <p class="contact__line">www.marloweadvisory.example</p>
    </div>
  </article>

  <article class="card card--back">
    <div class="wordmark">
      <span class="wordmark__square" aria-hidden="true"></span>
      <span class="wordmark__name">Marlowe Advisory</span>
    </div>
  </article>
</body>
</html>
```